Pre-workout label and Super Greens label for Brightmoor Nutrition Supplements

I need a label design for Club Brightmoor's 2 supplements. The first is a Pre-workout. The Pre-workout label needs to be 11.25 x 2.5 inches. This label will go on a black container. The second is a Super-Green. The Super-Green label should be 11.25 x 4.25 inches and will go on a white container. We have been selling these for a few years but the current labels are a little meh. I'd like something trendier and bolder. Must keep the Club Brightmoor branding. All the nurtition data must appear . I attached the current designs so you can know the flavors, nutrtional data etc. Thank you!
Updates

I can upload the Club Brightmoor logo! If anyone can tell me how to do that.

```html
<!DOCTYPE html>
<html lang="en">
<head>
<meta charset="utf-8">
<title>Brightmoor Nutrition – Supplement Labels</title>
<link href="https://fonts.googleapis.com/css2?family=Oswald:wght@500&family=Russo+One&family=Barlow+Condensed:ital,wght@1,700&family=Arimo:wght@400;700&display=swap" rel="stylesheet">
<style>
:root{
  --ink:#121212;
  --paper:#ffffff;
  --label-light:#f2f2f2;
  --label-shade:#dcdcdc;
  --mint:#5ff0cb;
  --mint-line:#8fe8cf;
  --grey-text:#5a5a5a;
  --red-deep:#4a0709;
  --red:#8a1014;
  --red-mid:#a4161b;
  --red-bright:#d8222b;
  --pink-text:#f1b9bb;
  --divider:#c9c9c9;
}
*{box-sizing:border-box;margin:0;padding:0}
html,body{width:1200px;height:2400px;overflow:hidden;background:var(--paper)}
body{position:relative;font-family:"Arimo",Arial,sans-serif;color:var(--ink)}

/* brand header */
.brand-header{position:absolute;top:58px;left:0;width:1200px;text-align:center}
.brand-header .brand-square{display:block;width:56px;height:56px;margin:0 auto 26px;background:var(--red-bright)}
.brand-header .brand-name{font-family:"Oswald",sans-serif;font-weight:500;font-size:30px;letter-spacing:2px}

.brand-mark{display:flex;flex-direction:column;align-items:center;gap:6px}
.brand-mark .brand-square{width:16px;height:16px;background:var(--red-bright)}
.brand-mark .brand-name{font-family:"Oswald",sans-serif;font-weight:500;letter-spacing:1px}

/* label backgrounds */
.label-bg-light{background:linear-gradient(115deg,var(--label-light) 0%,#fafafa 30%,var(--label-shade) 55%,#f7f7f7 75%,#e6e6e6 100%)}
.label-bg-red{background:linear-gradient(160deg,var(--red-deep) 0%,var(--red) 35%,var(--red-mid) 55%,var(--red-deep) 80%,#6b0c10 100%)}
.bg-art{position:absolute;inset:0}

/* super green front panel */
.sg-front{position:absolute;width:380px;height:337px;transform-origin:top left}
.sg-front .brand-mark{position:absolute;top:26px;left:0;width:100%}
.sg-front .brand-name{font-size:14px}
.product-title{font-family:"Russo One",sans-serif;font-style:normal;display:block;text-align:center;transform:skewX(-12deg);white-space:nowrap}
.sg-front .product-title{position:absolute;top:98px;left:0;width:100%;font-size:40px;color:var(--ink)}
.flavor-tag{position:absolute;left:50%;transform:translateX(-50%) skewX(-18deg);font-family:"Barlow Condensed",sans-serif;font-weight:700;font-style:italic;letter-spacing:1px;white-space:nowrap}
.sg-front .flavor-tag{top:162px;background:var(--mint);color:var(--ink);font-size:15px;padding:3px 16px}
.benefits{position:absolute;left:0;width:100%;display:flex;justify-content:center}
.benefit{display:flex;flex-direction:column;align-items:center;text-align:center;text-transform:uppercase}
.sg-front .benefits{top:206px;gap:22px}
.sg-front .benefit{width:92px}
.sg-front .benefit svg{width:36px;height:36px;margin-bottom:20px}
.sg-front .benefit-text{font-size:9px;line-height:1.15;color:var(--grey-text);letter-spacing:.5px}
.pack-info{position:absolute;left:40px;right:40px;display:flex;justify-content:space-between;font-weight:700}
.sg-front .pack-info{top:300px;font-size:8.5px}

/* pre-workout front panel */
.pw-front{position:absolute;width:320px;height:172px;transform-origin:top left;color:#fff}
.pw-front .brand-mark{position:absolute;top:10px;left:0;width:100%;gap:3px}
.pw-front .brand-mark .brand-square{width:11px;height:11px;background:#fff}
.pw-front .brand-name{font-size:8px;color:#fff}
.pw-front .product-title{position:absolute;top:34px;left:0;width:100%;font-size:31px;color:#fff}
.pw-front .flavor-tag{top:76px;background:var(--red-bright);font-size:10px;padding:1px 10px;color:#fff}
.pw-front .benefits{top:100px;gap:18px}
.pw-front .benefit{width:64px}
.pw-front .benefit svg{width:15px;height:15px;margin-bottom:5px}
.pw-front .benefit-text{font-family:"Arimo",sans-serif;font-size:7px;letter-spacing:.3px}
.pw-front .benefit-sub{font-size:5.5px;color:var(--pink-text)}
.pw-front .pack-info{top:158px;left:48px;right:48px;font-family:"Oswald",sans-serif;font-size:6px;letter-spacing:.5px}

/* positioned pieces */
.sg-label-front{position:absolute;left:428px;top:390px;width:343px;height:328px;overflow:hidden}
.pw-label-front{position:absolute;left:459px;top:900px;width:308px;height:157px;overflow:hidden}
.section-divider{position:absolute;left:374px;top:1285px;width:487px;height:1px;background:var(--divider)}
.sg-wrap{position:absolute;left:169px;top:1516px;width:893px;height:337px;overflow:hidden;border:1px solid #e2e2e2}
.pw-wrap{position:absolute;left:221px;top:2048px;width:764px;height:172px;overflow:hidden}

/* info boxes */
.info-box{position:absolute;border:1px solid var(--mint-line);border-radius:7px;padding:10px 12px 8px 15px;font-size:8.4px;line-height:1.28}
.pw-wrap .info-box{border-color:#d88a8d;color:#fff;font-size:3.9px;line-height:1.3;padding:5px 6px;border-radius:5px}
.info-box b{font-weight:700}
.disclaimer{font-weight:700;text-align:center}

/* supplement facts */
.facts{position:absolute;font-size:4.3px;line-height:1.25}
.facts-table{background:#fff;border:1px solid var(--ink);padding:3px 3px 2px}
.facts-title{font-weight:700;font-size:8px;line-height:1.1}
.facts-row{display:flex;justify-content:space-between;border-top:.5px solid #777;padding:.5px 0}
.facts-row.thick{border-top:1.5px solid var(--ink)}
.facts-row span:first-child{flex:1;padding-right:4px}
.facts-row span+span{width:24px;text-align:right}
.facts-row.indent span:first-child{padding-left:4px}
.facts-notes{margin-top:3px}
.pw-wrap .facts{color:#fff}
.pw-wrap .facts-table{color:var(--ink)}
</style>
</head>
<body>

<header class="brand-header">
  <span class="brand-square"></span>
  <span class="brand-name">BRIGHTMOOR NUTRITION</span>
</header>

<!-- Super Green front -->
<section class="sg-label-front label-bg-light">
  <div class="bg-art" role="img" aria-label="Soft white and grey flowing wave background"></div>
  <div class="sg-front" style="transform:scale(.9)">
    <div class="brand-mark"><span class="brand-square"></span><span class="brand-name">BRIGHTMOOR NUTRITION</span></div>
    <h1 class="product-title">SUPER GREEN</h1>
    <div class="flavor-tag">APPLE CINNAMON</div>
    <div class="benefits">
      <div class="benefit"><svg viewBox="0 0 36 36"><path d="M18 18c-4-6-12-6-12 0s8 6 12 0 12-6 12 0-8 6-12 0z" fill="none" stroke="var(--mint)" stroke-width="4"/></svg><span class="benefit-text">Detox<br>Body *</span></div>
      <div class="benefit"><svg viewBox="0 0 36 36"><path d="M18 2v5h-6a3 3 0 000 6h12a3 3 0 010 6H12a3 3 0 000 6h12a3 3 0 010 6h-6v3" fill="none" stroke="var(--mint)" stroke-width="3" stroke-linecap="round"/></svg><span class="benefit-text">Promote Healthy<br>Digestion *</span></div>
      <div class="benefit"><svg viewBox="0 0 36 36"><path d="M18 2l13 5v10c0 9-6 14-13 17C11 31 5 26 5 17V7z" fill="var(--mint)"/><path d="M18 11v13M11.5 17.5h13" stroke="#fff" stroke-width="4"/></svg><span class="benefit-text">Support<br>Immunity *</span></div>
    </div>
    <div class="pack-info"><span>Dietary Supplement</span><span>30 Servings&nbsp; 270g (9.5oz)</span></div>
  </div>
</section>

<!-- Pre-Workout front -->
<section class="pw-label-front label-bg-red">
  <div class="bg-art" role="img" aria-label="Dark red layered wave background"></div>
  <div class="pw-front" style="transform:scale(.9625,.913)">
    <div class="brand-mark"><span class="brand-square"></span><span class="brand-name">BRIGHTMOOR NUTRITION</span></div>
    <h2 class="product-title">PRE-WORKOUT</h2>
    <div class="flavor-tag">WATERMELON SUGAR</div>
    <div class="benefits">
      <div class="benefit"><svg viewBox="0 0 16 16"><rect width="16" height="16" fill="#222"/><path d="M9 2L4 9h4l-1 5 5-7H8z" fill="#fff"/></svg><span class="benefit-text">Energy*</span><span class="benefit-sub">CAFFEINE</span></div>
      <div class="benefit"><svg viewBox="0 0 16 16"><rect width="16" height="16" fill="#222"/><path d="M8 3l4 5H9.5v5h-3V8H4z" fill="#fff"/></svg><span class="benefit-text">Performance*</span><span class="benefit-sub">BETA-ALANINE</span></div>
      <div class="benefit"><svg viewBox="0 0 16 16"><rect width="16" height="16" fill="#222"/><path d="M3 5v6M5 4v8M11 4v8M13 5v6M5 8h6" stroke="#fff" stroke-width="1.5"/></svg><span class="benefit-text">Strength*</span><span class="benefit-sub">CREATINE</span></div>
    </div>
    <div class="pack-info"><span>DIETARY SUPPLEMENT</span><span>30 SERVINGS 240g (8.5oz)</span></div>
  </div>
</section>

<div class="section-divider"></div>

<!-- Super Green full wrap -->
<section class="sg-wrap label-bg-light">
  <div class="bg-art" role="img" aria-label="Soft white and grey flowing wave background"></div>

  <div class="info-box" style="left:51px;top:28px;width:136px;height:58px"><b>Directions:</b> Mix one (1) scoop into 6-8oz of your favorite non-citrus juice, water, smoothie, or protein shake.</div>
  <div class="info-box" style="left:51px;top:104px;width:136px;height:106px"><b>CAUTION:</b> As with any dietary supplement, consult your healthcare practitioner before using this product, especially if you are pregnant, nursing, anticipate surgery, take medication on a regular basis or are otherwise under medical supervision. Store in a cool, dry place. Keep out of reach of children.</div>
  <div class="info-box disclaimer" style="left:51px;top:272px;width:136px;height:25px;font-size:4.6px;line-height:1.2;padding:4px 6px">*These statements have not been evaluated by the Food and Drug Administration. This product is not intended to diagnose, treat, cure or prevent any disease.</div>

  <div class="sg-front" style="left:256px;top:0">
    <div class="brand-mark"><span class="brand-square"></span><span class="brand-name">BRIGHTMOOR NUTRITION</span></div>
    <h2 class="product-title">SUPER GREEN</h2>
    <div class="flavor-tag">APPLE CINNAMON</div>
    <div class="benefits">
      <div class="benefit"><svg viewBox="0 0 36 36"><path d="M18 18c-4-6-12-6-12 0s8 6 12 0 12-6 12 0-8 6-12 0z" fill="none" stroke="var(--mint)" stroke-width="4"/></svg><span class="benefit-text">Detox<br>Body *</span></div>
      <div class="benefit"><svg viewBox="0 0 36 36"><path d="M18 2v5h-6a3 3 0 000 6h12a3 3 0 010 6H12a3 3 0 000 6h12a3 3 0 010 6h-6v3" fill="none" stroke="var(--mint)" stroke-width="3" stroke-linecap="round"/></svg><span class="benefit-text">Promote Healthy<br>Digestion *</span></div>
      <div class="benefit"><svg viewBox="0 0 36 36"><path d="M18 2l13 5v10c0 9-6 14-13 17C11 31 5 26 5 17V7z" fill="var(--mint)"/><path d="M18 11v13M11.5 17.5h13" stroke="#fff" stroke-width="4"/></svg><span class="benefit-text">Support<br>Immunity *</span></div>
    </div>
    <div class="pack-info"><span>Dietary Supplement</span><span>30 Servings&nbsp; 270g (9.5oz)</span></div>
  </div>

  <div class="facts" style="left:700px;top:43px;width:166px">
    <div class="facts-table">
      <div class="facts-title">Supplement Facts</div>
      <div>Serving Size: Approx. 1 Scoop (9 g)<br>Servings per Container: 30</div>
      <div class="facts-row thick"><span></span><span>Amount</span><span>%DV</span></div>
      <div class="facts-row"><span>Calories</span><span>40</span><span></span></div>
      <div class="facts-row"><span>Total Carbohydrate</span><span>9 g</span><span>3%</span></div>
      <div class="facts-row indent"><span>Dietary Fiber</span><span>2 g</span><span>7%</span></div>
      <div class="facts-row indent"><span>Total Sugars</span><span>&lt;1 g</span><span></span></div>
      <div class="facts-row"><span>Protein</span><span>2 g</span><span></span></div>
      <div class="facts-row"><span>Vitamin E (as Tocopheryl Acetate)</span><span>46 mg</span><span>307%</span></div>
      <div class="facts-row"><span>Calcium</span><span>30 mg</span><span>2%</span></div>
      <div class="facts-row"><span>Iron</span><span>2.5 mg</span><span>14%</span></div>
      <div class="facts-row"><span>Sodium</span><span>15 mg</span><span>1%</span></div>
      <div class="facts-row"><span>Potassium</span><span>110 mg</span><span>2%</span></div>
      <div class="facts-row thick"><span><b>Green Health Blend</b><br>Soy Lecithin, Apple Fruit, Barley Grass, Alfalfa Herb, Wheat Grass, Wheat Sprout, Barley Malt, Rice Bran, Dulse, Spinach Leaf</span><span>5.6 g</span><span>†</span></div>
      <div class="facts-row"><span><b>Energy Blend</b><br>Spirulina Whole Plant, Beet Root, Bee Pollen, Green Tea Leaf Extract</span><span>1.41 g</span><span>†</span></div>
      <div class="facts-row"><span><b>Detox Blend</b><br>Acerola Berry, Parsley Leaf, Licorice Root, Echinacea, Astragalus Root, Milk Thistle Seed Extract</span><span>420 mg</span><span>†</span></div>
      <div class="facts-row"><span><b>Alkalinity Blend</b><br>Chlorella Cell Wall, Suma Root, Ginkgo Leaf Extract, Grape Seed Extract</span><span>340 mg</span><span>†</span></div>
      <div class="facts-row"><span><b>Probiotic Blend Complex</b><br>Lactobacillus acidophilus, L. bulgaricus, Bifidobacterium bifidum, B. longum, S. thermophilus</span><span>150 mg</span><span>†</span></div>
      <div class="facts-row"><span><b>Enzyme Blend</b><br>Maltodextrin, Inulin, Bromelain, Papain, Cellulase, Lipase, Protease</span><span>125 mg</span><span>†</span></div>
      <div class="facts-row thick"><span>Percent Daily Values are based on a 2,000 calorie diet<br>† Daily Value (DV) not established</span></div>
    </div>
    <div class="facts-notes"><b>Other Ingredients:</b> Organic Cassia Bark Powder, Natural Flavor, Silicon Dioxide, Rebaudioside A (From Stevia Leaf Extract), Sucralose.<br>Contains: Tree Nuts (Ginkgo Nut), Wheat, and Soy.<br><b>Formulated by:</b> Club Brightmoor, 48 Harrow Lane, Fenwick, OR 97000 (555) 014-2290</div>
  </div>
</section>

<!-- Pre-Workout full wrap -->
<section class="pw-wrap label-bg-red">
  <div class="bg-art" role="img" aria-label="Dark red layered wave background"></div>

  <div class="info-box" style="left:24px;top:31px;width:128px;height:78px"><b>Directions:</b> Use on training days only. Mix 1 scoop with 8-10 oz of cold water 15-30 minutes prior to training.<br><b>Warning:</b> Not intended for use by persons under age 18. Do not exceed recommended dose. Do not combine with other sources of caffeine, including coffee, tea, soda or other supplements. Contains caffeine. Use in a 12 week cycle, then 2 weeks off. Consult your physician prior to use if you are pregnant, nursing, taking medication, or have a medical condition including heart, liver, kidney or thyroid disease, high blood pressure, anxiety or diabetes. Discontinue use 2 weeks prior to surgery or if you experience rapid heartbeat, dizziness or severe headache. Keep out of reach of children.</div>
  <div class="info-box disclaimer" style="left:24px;top:117px;width:75px;height:19px">*These statements have not been evaluated by the Food and Drug Administration. This product is not intended to diagnose, treat, cure or prevent any disease.</div>

  <div class="pw-front" style="left:222px;top:0">
    <div class="brand-mark"><span class="brand-square"></span><span class="brand-name">BRIGHTMOOR NUTRITION</span></div>
    <h2 class="product-title">PRE-WORKOUT</h2>
    <div class="flavor-tag">WATERMELON SUGAR</div>
    <div class="benefits">
      <div class="benefit"><svg viewBox="0 0 16 16"><rect width="16" height="16" fill="#222"/><path d="M9 2L4 9h4l-1 5 5-7H8z" fill="#fff"/></svg><span class="benefit-text">Energy*</span><span class="benefit-sub">CAFFEINE</span></div>
      <div class="benefit"><svg viewBox="0 0 16 16"><rect width="16" height="16" fill="#222"/><path d="M8 3l4 5H9.5v5h-3V8H4z" fill="#fff"/></svg><span class="benefit-text">Performance*</span><span class="benefit-sub">BETA-ALANINE</span></div>
      <div class="benefit"><svg viewBox="0 0 16 16"><rect width="16" height="16" fill="#222"/><path d="M3 5v6M5 4v8M11 4v8M13 5v6M5 8h6" stroke="#fff" stroke-width="1.5"/></svg><span class="benefit-text">Strength*</span><span class="benefit-sub">CREATINE</span></div>
    </div>
    <div class="pack-info"><span>DIETARY SUPPLEMENT</span><span>30 SERVINGS 240g (8.5oz)</span></div>
  </div>

  <div class="facts" style="left:587px;top:33px;width:144px;font-size:3.6px">
    <div class="facts-table">
      <div class="facts-title" style="font-size:5.5px">Supplement Facts</div>
      <div class="facts-row thick"><span></span><span>Amount</span><span>%DV</span></div>
      <div class="facts-row"><span>Vitamin B6 (as Pyridoxal 5' Phosphate)</span><span>0.2 mg</span><span>2%</span></div>
      <div class="facts-row"><span>Folate (as Methylfolate)</span><span>250 mcg</span><span>63%</span></div>
      <div class="facts-row"><span>Vitamin B12 (as Methylcobalamin)</span><span>20 mcg</span><span>833%</span></div>
      <div class="facts-row"><span>Beta-Alanine</span><span>1.6 g</span><span>†</span></div>
      <div class="facts-row"><span>Creatine Monohydrate</span><span>1 g</span><span>†</span></div>
      <div class="facts-row"><span>L-Arginine Alpha-Ketoglutarate</span><span>1 g</span><span>†</span></div>
      <div class="facts-row"><span>L-Citrulline</span><span>1 g</span><span>†</span></div>
      <div class="facts-row"><span>Betaine Anhydrous</span><span>500 mg</span><span>†</span></div>
      <div class="facts-row"><span>Caffeine Anhydrous</span><span>250 mg</span><span>†</span></div>
      <div class="facts-row"><span>Huperzine A</span><span>40 mcg</span><span>†</span></div>
      <div class="facts-row thick"><span>† Daily Value (DV) not established</span></div>
    </div>
    <div class="facts-notes"><b>Other Ingredients:</b> Citric Acid, Pineapple Fruit Juice Powder, Silicon Dioxide, Natural and Artificial Flavors, Acesulfame Potassium, Sucralose, and FD&amp;C Red #40.<br><br><b>Formulated by:</b> Club Brightmoor, 48 Harrow Lane, Fenwick, OR 97000 (555) 014-2290</div>
  </div>
</section>

</body>
</html>
```